Flat Belly Design Graphics for Social

I want to create 9 social media graphics (new Instagram size 4:5 (1080 x 1350 pixels) focusing on our Flat Belly Graphics, using the pics attached. Use the attached pics, NO RANDOM STOCK PHOTOGRAPHY. For the color scheme of the graphics, the color palette is attached. YOU MUST POST ALL 9 GRAPHICS IN ONE ENTRY.
Using the 3 titles below, create one set of graphics. 1) with all text, then for the others, use the pictures as detailed below in IMPORTANT:
1. Ten-Week Bright Morning Reboot
2. The Quick Garden Kitchen Menu Guide
3. Studio Habits for Lasting Energy Past Midlife - Zero Gym Needed
IMPORTANT:
Only use RK Pic 1 and RK Pic 2 with the title, Ten-Week Bright Morning Reboot
Only use meal plan1 and meal plan2 pics with the title, Quick Garden Kitchen Menu Guide
Only use studio habits 1 and studio habits 2 pics with the title, Studio Habits for Lasting Energy Past Midlife - Zero Gym Needed
women over 40

```html
<!DOCTYPE html>
<html lang="en">
<head>
<meta charset="utf-8">
<title>Morning Reboot Social Set</title>
<link href="https://fonts.googleapis.com/css2?family=Oswald:wght@300;500;700&display=swap" rel="stylesheet">
<style>
  :root {
    --backdrop: #1a0509;
    --slate-green: #2f4f4c;
    --title-green: #1b5a4c;
    --blush: #f9d9e2;
    --shell: #fbeced;
    --rose: #e096ad;
    --ink: #111111;
    --white: #ffffff;
  }
  html, body { margin: 0; padding: 0; overflow: hidden; }
  body { background: var(--backdrop); }
  .canvas {
    position: relative; width: 1074px; height: 1200px; overflow: hidden;
    background: var(--backdrop);
    font-family: "Oswald", "Arial Narrow", sans-serif;
  }
  .tile {
    position: absolute; width: 263px; height: 324px; overflow: hidden;
    background: var(--shell);
  }
  .col-1 { left: 128px; } .col-2 { left: 412px; } .col-3 { left: 699px; }
  .row-1 { top: 94px; } .row-2 { top: 438px; } .row-3 { top: 782px; }
  .tile svg.shapes { position: absolute; inset: 0; width: 263px; height: 324px; }
  .photo {
    position: absolute; border-radius: 50%;
    background: radial-gradient(circle at 50% 40%, #d9b9a6 0%, #8a6a5a 55%, #3b2c28 100%);
  }
  .photo.food { background: radial-gradient(circle at 55% 50%, #e8e2d6 0%, #a2643a 45%, #4a2e20 100%); }
  .photo.kitchen { background: radial-gradient(circle at 50% 45%, #f1ebe6 0%, #b38a6c 55%, #4b3426 100%); }
  .photo.friends { background: radial-gradient(circle at 50% 45%, #f4dfd3 0%, #c79a80 50%, #6b4a3c 100%); }

  .stack { position: absolute; line-height: 0.92; margin: 0; }
  .stack span { display: block; white-space: nowrap; }
  .center-stack { left: 0; right: 0; text-align: center; }
  .thin { font-weight: 300; color: var(--slate-green); }
  .heavy { font-weight: 700; color: var(--title-green); letter-spacing: -0.5px; }
  .medium { font-weight: 700; color: var(--ink); }
  .pink-text { color: var(--rose); font-weight: 700; }
  .stack .pill {
    display: inline-block; border-radius: 999px; color: var(--white);
    font-weight: 500; letter-spacing: -0.2px; line-height: 1.2;
  }
  .pill.rose { background: var(--rose); }
  .pill.slate { background: var(--slate-green); }
  .right-stack { right: 22px; text-align: right; }
  .tagline { font-weight: 300; color: var(--ink); font-size: 14px; line-height: 1.15; margin-top: 3px; }
</style>
</head>
<body>
<main class="canvas">

  <!-- Row 1: all-text covers -->
  <section class="tile col-1 row-1" style="background: var(--slate-green);">
    <svg class="shapes" viewBox="0 0 263 324"><path d="M0 324 V112 A131.5 88 0 0 1 263 112 V324 Z" fill="var(--blush)"/></svg>
    <h2 class="stack center-stack" style="top:64px;">
      <span class="thin" style="font-size:32px;">Ten-Week</span>
      <span class="heavy" style="font-size:62px;">BRIGHT</span>
      <span class="heavy" style="font-size:52px;">MORNING</span>
      <span class="thin" style="font-size:32px;">Reboot</span>
    </h2>
  </section>

  <section class="tile col-2 row-1" style="background: var(--slate-green);">
    <svg class="shapes" viewBox="0 0 263 324">
      <rect x="0" y="0" width="263" height="165" fill="var(--blush)"/>
      <circle cx="131.5" cy="162" r="138" fill="var(--blush)"/>
    </svg>
    <h2 class="stack center-stack" style="top:42px;">
      <span class="thin" style="font-size:27px;">The Quick</span>
      <span class="heavy" style="font-size:64px;">GARDEN</span>
      <span class="heavy" style="font-size:54px;">KITCHEN</span>
      <span class="thin" style="font-size:33px;">MENU GUIDE</span>
    </h2>
  </section>

  <section class="tile col-3 row-1" style="background: var(--slate-green);">
    <svg class="shapes" viewBox="0 0 263 324"><path d="M0 324 V112 A131.5 88 0 0 1 263 112 V324 Z" fill="var(--blush)"/></svg>
    <div class="stack center-stack" style="top:69px;">
      <span><span class="pill rose" style="font-size:14px; padding:3px 20px;">Studio Habits for</span></span>
    </div>
    <h2 class="stack center-stack" style="top:106px;">
      <span class="heavy" style="font-size:70px;">LASTING</span>
      <span class="heavy" style="font-size:70px;">ENERGY</span>
    </h2>
    <div class="stack center-stack" style="top:265px;">
      <span><span class="pill slate" style="font-size:11px; padding:2px 10px;">Past Midlife - Zero Gym Needed</span></span>
    </div>
  </section>

  <!-- Row 2 -->
  <section class="tile col-1 row-2">
    <svg class="shapes" viewBox="0 0 263 324">
      <rect x="170" y="5" width="110" height="9" rx="4.5" fill="var(--slate-green)"/>
      <rect x="10" y="215" width="190" height="103" fill="var(--slate-green)"/>
      <circle cx="198" cy="205" r="112" fill="var(--rose)"/>
      <path d="M86 205 A112 112 0 0 0 310 205 Z" fill="var(--slate-green)"/>
      <circle cx="198" cy="205" r="104" fill="var(--white)"/>
    </svg>
    <div class="photo" role="img" aria-label="Smiling woman in a white cropped sweater pointing toward her waist" style="left:100px; top:107px; width:196px; height:196px;"></div>
    <h2 class="stack" style="left:21px; top:14px;">
      <span class="pink-text" style="font-size:18px;">Ten-Week</span>
      <span class="heavy" style="font-size:38px;">Bright</span>
      <span class="heavy" style="font-size:38px;">Morning</span>
    </h2>
    <p class="stack" style="left:24px; top:241px;">
      <span class="pink-text" style="font-size:27px;">Reboot</span>
    </p>
  </section>

  <section class="tile col-2 row-2">
    <svg class="shapes" viewBox="0 0 263 324">
      <rect x="187" y="0" width="76" height="324" fill="var(--slate-green)"/>
      <rect x="10" y="210" width="190" height="103" fill="var(--rose)"/>
      <circle cx="168" cy="206" r="108" fill="var(--slate-green)"/>
      <circle cx="168" cy="206" r="101" fill="var(--white)"/>
    </svg>
    <div class="photo food" role="img" aria-label="Overhead table of fresh produce, chicken and a handwritten meal plan sheet" style="left:72px; top:110px; width:192px; height:192px;"></div>
    <h2 class="stack" style="left:15px; top:18px;">
      <span class="heavy" style="font-size:26px;">The Quick</span>
      <span class="medium" style="font-size:24px; color:#1e2a28; letter-spacing:-0.3px;">GARDEN KITCHEN</span>
      <span class="heavy" style="font-size:26px;">Menu Guide</span>
    </h2>
  </section>

  <section class="tile col-3 row-2">
    <svg class="shapes" viewBox="0 0 263 324">
      <circle cx="175" cy="78" r="110" fill="var(--rose)"/>
      <circle cx="178" cy="78" r="104" fill="var(--white)"/>
    </svg>
    <div class="photo friends" role="img" aria-label="One woman whispering a secret to a delighted friend" style="left:80px; top:-20px; width:196px; height:196px;"></div>
    <h2 class="stack" style="left:27px; top:194px;">
      <span class="medium" style="font-size:26px;">Studio</span>
      <span class="medium" style="font-size:26px;">Habits for</span>
      <span class="heavy" style="font-size:31px;">LASTING ENERGY</span>
      <span class="tagline">Past Midlife - Zero Gym Needed</span>
    </h2>
  </section>

  <!-- Row 3 -->
  <section class="tile col-1 row-3">
    <svg class="shapes" viewBox="0 0 263 324">
      <circle cx="172" cy="78" r="110" fill="var(--rose)"/>
      <circle cx="178" cy="78" r="104" fill="var(--white)"/>
    </svg>
    <div class="photo kitchen" role="img" aria-label="Smiling woman in a white cropped sweater standing in a kitchen" style="left:82px; top:-20px; width:196px; height:196px;"></div>
    <h2 class="stack" style="left:21px; top:200px;">
      <span class="medium" style="font-size:27px;">Ten-Week</span>
      <span class="heavy" style="font-size:30px;">BRIGHT MORNING</span>
      <span class="medium" style="font-size:27px;">Reboot</span>
    </h2>
  </section>

  <section class="tile col-2 row-3">
    <svg class="shapes" viewBox="0 0 263 324">
      <rect x="0" y="121" width="263" height="203" fill="var(--slate-green)"/>
      <circle cx="131" cy="109" r="98" fill="var(--slate-green)"/>
      <path d="M118 20 A90 90 0 0 0 118 198" fill="none" stroke="var(--white)" stroke-width="8"/>
      <circle cx="131" cy="109" r="87" fill="var(--white)"/>
    </svg>
    <div class="photo food" role="img" aria-label="Overhead spread of salmon, eggs, vegetables and a day-by-day meal plan notebook" style="left:48px; top:26px; width:166px; height:166px;"></div>
    <h2 class="stack right-stack" style="top:220px;">
      <span class="medium" style="font-size:24px; color:var(--white);">The Quick</span>
      <span class="medium" style="font-size:29px; color:var(--white);">GARDEN KITCHEN</span>
      <span class="medium" style="font-size:24px; color:var(--white);">Menu Guide</span>
    </h2>
  </section>

  <section class="tile col-3 row-3">
    <svg class="shapes" viewBox="0 0 263 324">
      <circle cx="118" cy="66" r="140" fill="var(--slate-green)"/>
      <circle cx="108" cy="66" r="136" fill="var(--blush)"/>
    </svg>
    <div class="photo friends" role="img" aria-label="Two women sharing a whispered secret, one looking surprised" style="left:10px; top:10px; width:190px; height:180px; border-radius:0 0 50% 50%; background:linear-gradient(180deg,#e9c9bd 0%,#b88b74 60%,#8ca3b6 100%);"></div>
    <h2 class="stack right-stack" style="top:194px;">
      <span class="medium" style="font-size:26px;">Studio</span>
      <span class="medium" style="font-size:26px;">Habits for</span>
      <span class="heavy" style="font-size:31px;">LASTING ENERGY</span>
      <span class="tagline">Past Midlife - Zero Gym Needed</span>
    </h2>
  </section>

</main>
</body>
</html>
```